Design of Labels for Harbour Reef Gin bottle

Design bottle labels for Harbour Reef Gin. There are three labels to design; a front, a back and a tamper band to be placed over the cork. The labels should be deigned to fit the bottle specified in the link below.
The Gin is an excellent high end premium brand Navy strength Gin 57% Vol. The bottle should evoke excellence and a romance of period of pride in the British Navy. Gin was drunk by officers in the Navy so a representation of the Officer Class should be made possibly through gold braid of a senior officer's sleeve, cap or lapel. The white ensign should also be prominent. Suggested colour themes are navy blues, grey, and white....although others schemes may be suitable. Corley's Dock Rum is a good example of the sort of thing we are looking for, although the design must not be so similar that it encroaches on Corley's trade mark or copyrights. The period theme is 1900 to 1940
Bottle link: https://www.vessel-crate-depot.co.uk/Glass-bottles/350ml-flint-glass-bottle-Marta.html
Target Market(s)
Gin Drinkers
Look and feel
Each slider illustrates characteristics of the customer's brand and the style your logo design should communicate.

```html
<!DOCTYPE html>
<html lang="en">
<head>
<meta charset="utf-8">
<title>Harbour Reef Gin – Labels</title>
<link rel="stylesheet" href="https://fonts.googleapis.com/css2?family=Cinzel:wght@400;700;900&display=swap">
<style>
  :root {
    --backdrop: #e6e6e8;
    --paper: #ffffff;
    --ink: #111111;
    --gold: #d9b36a;
    --gold-soft: #e8cf9e;
    --crimson: #b3262f;
    --navy: #1f3a7a;
  }
  html, body {
    margin: 0;
    padding: 0;
    width: 1200px;
    height: 1200px;
    overflow: hidden;
    background: var(--backdrop);
  }
  .canvas {
    width: 1200px;
    height: 1200px;
    display: flex;
    align-items: center;
    justify-content: center;
    gap: 90px;
    font-family: "Cinzel", "Times New Roman", serif;
    color: var(--ink);
  }

  /* Tamper band over the cork */
  .tamper-band {
    width: 160px;
    height: 560px;
    background: var(--paper);
    display: flex;
    flex-direction: column;
    align-items: center;
    justify-content: flex-end;
    padding-bottom: 80px;
    box-sizing: border-box;
    gap: 14px;
  }
  .tamper-band .mark-circle {
    width: 54px;
    height: 54px;
    border-radius: 50%;
    background: var(--crimson);
  }
  .tamper-band .mark-name {
    text-align: center;
    font-size: 15px;
    font-weight: 700;
    letter-spacing: 2px;
    line-height: 1.4;
    color: var(--navy);
  }

  /* Front label */
  .front-label {
    width: 700px;
    height: 880px;
    background: var(--paper);
    box-sizing: border-box;
    padding: 26px;
  }
  .label-frame {
    width: 100%;
    height: 100%;
    border: 3px solid var(--gold-soft);
    border-radius: 42px;
    box-sizing: border-box;
    display: flex;
    flex-direction: column;
    align-items: center;
  }
  .brand-top {
    margin: 118px 0 0;
    font-size: 76px;
    font-weight: 900;
    letter-spacing: 2px;
    line-height: 1;
  }
  .brand-mark {
    margin-top: 44px;
    display: flex;
    align-items: center;
    gap: 16px;
  }
  .brand-mark .mark-circle {
    width: 42px;
    height: 42px;
    border-radius: 50%;
    background: var(--crimson);
  }
  .brand-mark .mark-name {
    font-size: 26px;
    font-weight: 700;
    color: var(--navy);
    letter-spacing: 3px;
  }
  .brand-bottom {
    margin: 48px 0 0;
    font-size: 58px;
    font-weight: 900;
    letter-spacing: 2px;
    line-height: 1;
  }
  .rule-star {
    margin-top: 14px;
    width: 420px;
    height: 42px;
    display: block;
  }
  .tagline {
    margin: 16px 0 0;
    text-align: center;
    font-size: 19px;
    font-weight: 700;
    letter-spacing: 4px;
    line-height: 1.55;
  }
  .strength-bands {
    margin-top: 44px;
    display: flex;
    flex-direction: column;
    align-items: center;
    gap: 7px;
  }
  .band {
    width: 150px;
    height: 27px;
    display: flex;
    align-items: center;
    justify-content: center;
    color: var(--paper);
    font-size: 14px;
    font-weight: 700;
    letter-spacing: 2px;
  }
  .band-strength { background: var(--crimson); }
  .band-established { background: var(--navy); }
  .origin {
    margin: 18px 0 0;
    font-size: 12px;
    font-weight: 700;
    letter-spacing: 2px;
  }
</style>
</head>
<body>
  <main class="canvas">
    <section class="tamper-band" aria-label="Harbour Reef Gin tamper band">
      <span class="mark-circle"></span>
      <span class="mark-name">HARBOUR<br>REEF</span>
    </section>

    <section class="front-label" aria-label="Harbour Reef Gin front label">
      <div class="label-frame">
        <h1 class="brand-top">HARBOUR</h1>
        <div class="brand-mark">
          <span class="mark-circle"></span>
          <span class="mark-name">HARBOUR REEF</span>
        </div>
        <h2 class="brand-bottom">REEF GIN</h2>
        <svg class="rule-star" viewBox="0 0 420 42" aria-hidden="true">
          <line x1="0" y1="31" x2="420" y2="31" stroke="#111111" stroke-width="3"/>
          <polygon points="210,4 216,20 233,20 220,30 225,42 210,35 195,42 200,30 187,20 204,20" fill="#d9b36a"/>
        </svg>
        <p class="tagline">RICH HERITAGE<br>SMOOTH FLAVOUR</p>
        <div class="strength-bands">
          <span class="band band-strength">57% VOL</span>
          <span class="band band-established">EST 1920</span>
        </div>
        <p class="origin">MADE IN ENGLAND</p>
      </div>
    </section>
  </main>
</body>
</html>
```